Korvel Pharmacy, a pharmaceuticals distributor requires a redesigning of existing medicinal produ...

We require a refreshing, yet simple design that can be benchmarked against serious market leaders in this category of OTC and self-medication products , such as TALMO BREEZOL, a well known product which has similar applications as our product Quilra Zent.We are giving the old artwork, which now looks dull and colorless and requires some oomph! to appeal to even the younger generation.

Target Market(s)

All adults

Font styles to use
Decorative

Colors

Designer to choose colors to be used in the design.

Requirements
Must have
• A small image of menthol leaf
• An image of a lady's back(professional) that shows back pain on one of the box faces and on the opposite face an image of a man's shoulder showing shoulder pain or joint pain.

```html
<!DOCTYPE html>
<html lang="en">
<head>
<meta charset="utf-8">
<title>Quilra Zent Balm</title>
<link rel="stylesheet" href="https://fonts.googleapis.com/css2?family=Lilita+One&family=Roboto+Condensed:wght@300;700&family=Archivo:wght@800&display=swap">
<style>
  :root {
    --navy: #072176;
    --deep: #0a3a9e;
    --mid: #0b63c8;
    --cyan: #12b6ea;
    --band-a: #0cb6ea;
    --band-b: #038ed0;
    --ribbon: #e8141c;
    --ribbon-light: #ff5a5a;
    --white: #ffffff;
  }
  html, body { margin: 0; padding: 0; overflow: hidden; background: var(--navy); }
  .pack {
    position: relative;
    width: 842px;
    height: 1200px;
    overflow: hidden;
    background:
      radial-gradient(ellipse 300px 260px at 50% 44%, rgba(18,182,234,0.55), rgba(18,182,234,0) 100%),
      repeating-radial-gradient(circle at 50% 44%, rgba(18,182,234,0) 0 70px, rgba(18,182,234,0.28) 110px, rgba(18,182,234,0) 150px),
      radial-gradient(circle at 50% 44%, var(--mid) 0%, var(--deep) 45%, var(--navy) 85%);
  }
  .ribbon { position: absolute; left: 0; top: 26px; width: 275px; height: 145px; }
  .ribbon-label {
    position: absolute; left: 70px; top: 62px;
    font-family: "Archivo", sans-serif; font-weight: 800; font-size: 40px;
    color: var(--white); transform: rotate(-14deg) skewX(-10deg);
    letter-spacing: 1px;
  }
  .product-name {
    position: absolute; left: 0; right: 0; top: 295px;
    text-align: center;
    font-family: "Lilita One", sans-serif;
    color: var(--white);
    line-height: 1;
    margin: 0;
    font-weight: 400;
  }
  .product-name .line-1 { display: block; font-size: 170px; }
  .product-name .line-2 { display: block; font-size: 130px; margin-top: 10px; }
  .claim {
    position: absolute; left: 0; right: 0; top: 805px;
    text-align: center; color: var(--white);
    font-family: "Roboto Condensed", sans-serif;
    margin: 0;
  }
  .claim-intro { display: block; font-weight: 300; font-size: 58px; line-height: 66px; }
  .claim-uses { display: block; font-weight: 700; font-size: 56px; line-height: 66px; }
  .form-band {
    position: absolute; left: 0; right: 0; top: 1046px; height: 108px;
    background: linear-gradient(90deg, var(--band-b), var(--band-a) 45%, var(--band-b));
    display: flex; align-items: center; justify-content: center;
  }
  .form-label {
    font-family: "Archivo", sans-serif; font-weight: 800;
    font-size: 82px; color: var(--white); letter-spacing: 1px;
  }
</style>
</head>
<body>
<main class="pack">
  <svg class="ribbon" viewBox="0 0 275 145" aria-hidden="true">
    <defs>
      <linearGradient id="ribbonFill" x1="0" y1="0" x2="1" y2="0">
        <stop offset="0" stop-color="var(--ribbon)"/>
        <stop offset="1" stop-color="var(--ribbon-light)"/>
      </linearGradient>
    </defs>
    <path d="M0 55 Q120 45 258 2 L225 50 L272 88 Q150 96 0 142 Z" fill="url(#ribbonFill)"/>
  </svg>
  <span class="ribbon-label">NEW</span>

  <h1 class="product-name">
    <span class="line-1">Quilra</span>
    <span class="line-2">Zent</span>
  </h1>

  <p class="claim">
    <span class="claim-intro">For the Relief of</span>
    <span class="claim-uses">Mascular Aches &amp; Pains,</span>
    <span class="claim-uses">Nasal Congestion &amp; Catarrh</span>
  </p>

  <div class="form-band"><span class="form-label">BALM</span></div>
</main>
</body>
</html>
```